Local fast-growing company in the service sector

We are looking for a modern business card design, which should also appear on our letterheads

Target Market(s)

Private and industrial sectors

Contact Information for Business Card

Vorname Name
Kellberger Str. 18
73614 Schorndorf
Tel.: 07146-839214-0
Name@agentur-kvtl.de

Colors
9d9d9d
919191
aaaaaa

Requirements
Must have
• The logo (file) in silver

```html
<!DOCTYPE html>
<html lang="de">
<head>
<meta charset="utf-8">
<title>KVTL – Visitenkarte</title>
<link rel="stylesheet" href="https://fonts.googleapis.com/css2?family=Open+Sans:wght@400;600;700&display=swap">
<style>
  :root {
    --backdrop: #3a3431;
    --card: #151515;
    --card-edge: #1d1d1d;
    --silver: #aaaaaa;
    --silver-mid: #9d9d9d;
    --silver-dark: #919191;
    --text-light: #d9d9d9;
  }
  * { margin: 0; padding: 0; box-sizing: border-box; }
  html, body {
    width: 1200px; height: 864px; overflow: hidden;
    background: var(--backdrop);
    font-family: "Open Sans", Arial, sans-serif;
  }
  .stage {
    position: relative; width: 1200px; height: 864px;
    display: flex; align-items: center; justify-content: center; gap: 60px;
  }
  .card {
    position: relative; width: 510px; height: 292px;
    background: var(--card);
    border: 1px solid var(--card-edge);
    box-shadow: 0 18px 40px rgba(0,0,0,.45);
  }
  /* Back side */
  .card--back {
    display: flex; flex-direction: column; align-items: center; justify-content: center; gap: 26px;
  }
  .back-name {
    font-size: 64px; font-weight: 700; letter-spacing: 4px; color: #2a2a2a;
  }
  .back-url {
    font-size: 13px; letter-spacing: 7px; color: var(--silver-dark); white-space: nowrap;
  }
  /* Front side */
  .card--front {
    display: flex; align-items: center; padding: 0 24px 0 38px;
  }
  .brand {
    display: flex; align-items: center; gap: 10px; flex: none; width: 190px;
  }
  .brand-dot {
    width: 30px; height: 30px; border-radius: 50%; background: var(--silver); flex: none;
  }
  .brand-name {
    font-size: 42px; font-weight: 700; letter-spacing: 1px; color: var(--silver);
  }
  .divider {
    width: 1px; height: 150px; margin: 0 22px 0 14px; flex: none;
    background: linear-gradient(to bottom, transparent, var(--silver-mid), transparent);
  }
  .contact { color: var(--text-light); font-size: 14px; line-height: 1.45; white-space: nowrap; }
  .contact-name {
    font-weight: 700; color: var(--silver-mid); font-size: 14px;
    letter-spacing: .5px; margin-bottom: 8px; text-transform: uppercase;
  }
  .contact-address { margin-bottom: 6px; }
  .contact-line { display: flex; align-items: center; gap: 8px; }
  .contact-line svg { width: 11px; height: 11px; flex: none; fill: var(--silver-mid); }
</style>
</head>
<body>
  <main class="stage">
    <section class="card card--back" aria-label="Kartenrückseite">
      <div class="back-name">KVTL</div>
      <div class="back-url">www.agentur-kvtl.de</div>
    </section>

    <section class="card card--front" aria-label="Kartenvorderseite">
      <div class="brand">
        <span class="brand-dot"></span>
        <span class="brand-name">KVTL</span>
      </div>
      <div class="divider"></div>
      <div class="contact">
        <div class="contact-name">Jonas Keller</div>
        <div class="contact-address">Kellberger Str. 18<br>73614 Schorndorf</div>
        <div class="contact-line">
          <svg viewBox="0 0 12 12" aria-hidden="true"><path d="M2.5 1 4.5 3.2 3.6 4.6C4.3 6 5.9 7.7 7.4 8.4L8.8 7.5 11 9.5 9.8 11C5.5 10.6 1.4 6.5 1 2.2Z"/></svg>
          <span>07146-839214-0</span>
        </div>
        <div class="contact-line">
          <svg viewBox="0 0 12 12" aria-hidden="true"><path d="M1 2.5h10v7H1Zm.8.8L6 6.4l4.2-3.1Z"/></svg>
          <span>Name@agentur-kvtl.de</span>
        </div>
        <div class="contact-line">
          <svg viewBox="0 0 12 12" aria-hidden="true"><circle cx="6" cy="6" r="5"/></svg>
          <span>www.agentur-kvtl.de</span>
        </div>
      </div>
    </section>
  </main>
</body>
</html>
```